Disability provider requiring digital flyer to promote services

My company works within the Disability sector (KTAP registered provider), currently operating in Sydney, Australia.
I require a digital brochure which lists our services and gives potential customers a quick look into what we do with a single glance.
Undecided whether this digital flyer is to be single or double sided, happy to consult with an experienced designer in this regard.
I prefer minimalist designs (which may be an issue for someone trying to convey information, I'm not sure), and possibly someone who can work with out watercolor logo.
Services include:
-Supported Independent Living
-Specialist Disability Accommodation
-Individualised Living Options Stage 1 & 2
-Home Modifications
-Occupational Therapy
-Support Coordination Levels 1 & 2
-Short Term Accommodation - STA Respite
-Drop In Supports
-Community Access
Disability

```html
<!DOCTYPE html>
<html lang="en">
<head>
<meta charset="utf-8">
<title>Clearview Care – Disability Services Flyer</title>
<link rel="stylesheet" href="https://fonts.googleapis.com/css2?family=Bebas+Neue&family=Poppins:wght@300;400;600;700&display=swap">
<style>
  :root {
    --teal: #17cfad;
    --teal-dark: #0fb596;
    --pink: #f7157f;
    --orange: #f98b4c;
    --purple: #7a5bc6;
    --purple-dark: #4a2f86;
    --ink: #141414;
    --paper: #ffffff;
    --backdrop: #eeeeee;
    --rule: #bdbdbd;
  }
  * { box-sizing: border-box; margin: 0; padding: 0; }
  html, body { width: 783px; height: 1200px; overflow: hidden; }
  body { background: var(--backdrop); font-family: 'Poppins', sans-serif; }

  .flyer {
    position: absolute; left: 0; top: 45px;
    width: 783px; height: 1110px;
    background: var(--paper); overflow: hidden;
    box-shadow: 0 4px 18px rgba(0,0,0,.18);
  }
  .hero-art { position: absolute; left: 0; top: 0; width: 783px; height: 1110px; }

  .brand-name {
    position: absolute; left: 58px; top: 140px;
    font-family: 'Poppins', sans-serif; font-weight: 300;
    font-size: 30px; letter-spacing: 1px; color: var(--ink);
  }
  .brand-mark {
    position: absolute; left: 58px; top: 60px;
    width: 64px; height: 64px; border-radius: 50%;
    background: var(--pink); opacity: .85;
  }

  .headline { position: absolute; left: 56px; top: 205px; font-family: 'Bebas Neue', sans-serif; line-height: .9; }
  .headline-main { display: block; font-size: 86px; color: var(--teal); }
  .headline-sub { display: block; font-size: 56px; color: var(--ink); margin-top: 2px; }
  .headline-rule { position: absolute; left: 56px; top: 357px; width: 395px; height: 1px; background: var(--rule); }

  .intro {
    position: absolute; left: 56px; top: 376px; width: 520px;
    font-size: 22.5px; line-height: 28px; color: var(--ink);
  }

  .services {
    position: absolute; left: 57px; top: 464px; width: 668px; height: 520px;
    border: 2px solid var(--purple-dark); border-radius: 6px; background: var(--paper);
  }
  .services-tab {
    position: absolute; left: 179px; top: 450px; width: 424px; height: 66px;
  }
  .services-title {
    position: absolute; left: 179px; top: 457px; width: 424px; text-align: center;
    font-size: 35px; color: #fff; font-weight: 300; line-height: 46px;
  }
  .services-title strong { font-weight: 700; }

  .service {
    position: absolute; width: 190px; border-radius: 4px;
    color: #fff; font-weight: 600; font-size: 15.5px; line-height: 19px;
    text-align: center; display: flex; align-items: center; justify-content: center;
    padding: 26px 6px 0;
  }
  .service--pink { background: var(--pink); }
  .service--teal { background: var(--teal); }
  .service--orange { background: var(--orange); }
  .service-icon {
    position: absolute; left: 61px; top: -36px; width: 68px; height: 68px;
    border-radius: 50%; background: #fff; border: 4px solid var(--purple-dark);
  }
  .service-icon svg { width: 60px; height: 60px; }

  .col-1 { left: 80px; } .col-2 { left: 298px; } .col-3 { left: 516px; }
  .row-1 { top: 564px; height: 89px; }
  .row-2 { top: 707px; height: 90px; }
  .row-3 { top: 856px; height: 99px; }

  .contact { position: absolute; color: #fff; font-weight: 600; display: flex; align-items: center; gap: 10px; }
  .contact-phone { left: 60px; top: 1022px; font-size: 24px; }
  .contact-email { left: 60px; top: 1058px; font-size: 17px; }
  .contact svg { width: 18px; height: 18px; }

  .socials { position: absolute; left: 459px; top: 1026px; display: flex; gap: 6px; }
  .social-badge { width: 20px; height: 20px; border-radius: 3px; }
  .social-badge--round { border-radius: 50%; background: var(--purple-dark); }
  .web { position: absolute; left: 459px; top: 1058px; font-size: 15px; font-weight: 600; color: var(--ink); display: flex; align-items: center; gap: 6px; }
  .web svg { width: 15px; height: 15px; }
</style>
</head>
<body>
<main class="flyer">
  <svg class="hero-art" viewBox="0 0 783 1110" aria-hidden="false">
    <defs>
      <linearGradient id="park" x1="0" y1="0" x2="0" y2="1">
        <stop offset="0" stop-color="#7fa653"/>
        <stop offset=".55" stop-color="#b9c99a"/>
        <stop offset="1" stop-color="#2fae7e"/>
      </linearGradient>
    </defs>
    <path d="M300 0 C330 210 520 430 783 560 L783 0 Z" fill="var(--teal)"/>
    <path d="M500 520 C600 590 700 620 783 640 L783 560 C700 560 600 540 500 520 Z" fill="var(--teal)"/>
    <path d="M320 0 C360 200 530 400 783 500 L783 0 Z" fill="url(#park)" role="img" aria-label="Photo of a carer with an elderly woman in a wheelchair in a green park"/>
    <path d="M0 1000 L330 1000 C390 1000 420 1040 450 1110 L0 1110 Z" fill="var(--ink)"/>
  </svg>

  <span class="brand-mark" aria-hidden="true"></span>
  <div class="brand-name">Clearview Care</div>

  <h1 class="headline">
    <span class="headline-main">Disability</span>
    <span class="headline-sub">Provider Requiring</span>
  </h1>
  <div class="headline-rule"></div>

  <p class="intro">Clearview Care is a Sydney<br>based disability support services provider.</p>

  <section class="services" aria-label="Our services"></section>
  <svg class="services-tab" viewBox="0 0 424 66" aria-hidden="true">
    <path d="M0 2 L424 2 L400 20 C390 50 370 64 340 64 L84 64 C54 64 34 50 24 20 Z" fill="var(--purple)"/>
    <path d="M0 2 Q12 -2 24 20 L0 16 Z M424 2 Q412 -2 400 20 L424 16 Z" fill="var(--purple-dark)"/>
  </svg>
  <h2 class="services-title">OUR <strong>SERVICES</strong></h2>

  <div class="service service--pink col-1 row-1"><span class="service-icon"><svg viewBox="0 0 60 60" fill="none" stroke="var(--ink)" stroke-width="2"><path d="M22 40 L28 22 M28 22 L42 24 L38 32 L26 30"/><circle cx="22" cy="40" r="5"/></svg></span>Supported Independent Living</div>
  <div class="service service--teal col-2 row-1"><span class="service-icon"><svg viewBox="0 0 60 60" fill="none" stroke="var(--ink)" stroke-width="2"><circle cx="30" cy="16" r="3"/><path d="M28 22 L28 34 L38 34 L42 42"/><circle cx="28" cy="38" r="8"/></svg></span>Specialist Disability Accommodation</div>
  <div class="service service--orange col-3 row-1"><span class="service-icon"><svg viewBox="0 0 60 60" fill="none" stroke="var(--ink)" stroke-width="2"><rect x="30" y="28" width="16" height="12"/><rect x="16" y="20" width="10" height="20"/><path d="M14 40 H48"/></svg></span>Individualised Living Options Stage 1 &amp; 2</div>

  <div class="service service--pink col-1 row-2"><span class="service-icon"><svg viewBox="0 0 60 60" fill="none" stroke="var(--ink)" stroke-width="2"><rect x="16" y="18" width="28" height="24"/><path d="M20 26 H40 M20 32 H34"/></svg></span>Home Modifications</div>
  <div class="service service--teal col-2 row-2"><span class="service-icon"><svg viewBox="0 0 60 60" fill="none" stroke="var(--ink)" stroke-width="2"><circle cx="30" cy="22" r="7"/><path d="M20 44 L24 32 H36 L40 44"/></svg></span>Occupational Therapy</div>
  <div class="service service--orange col-3 row-2"><span class="service-icon"><svg viewBox="0 0 60 60" fill="none" stroke="var(--ink)" stroke-width="2"><circle cx="30" cy="30" r="8"/><circle cx="30" cy="30" r="14" stroke-dasharray="4 3"/></svg></span>Support Coordination Levels 1 &amp; 2</div>

  <div class="service service--pink col-1 row-3"><span class="service-icon"><svg viewBox="0 0 60 60" fill="none" stroke="var(--ink)" stroke-width="2"><path d="M16 30 L30 18 L44 30 M20 28 V42 H40 V28"/></svg></span>Short Term Accommodation STA Respite</div>
  <div class="service service--teal col-2 row-3"><span class="service-icon"><svg viewBox="0 0 60 60" fill="none" stroke="var(--ink)" stroke-width="2"><path d="M18 40 L28 28 L34 32 L42 22 M24 38 L32 30"/></svg></span>Drop In Supports</div>
  <div class="service service--orange col-3 row-3"><span class="service-icon"><svg viewBox="0 0 60 60" fill="none" stroke="var(--ink)" stroke-width="2"><rect x="24" y="24" width="12" height="12"/><circle cx="18" cy="18" r="3"/><circle cx="42" cy="18" r="3"/><circle cx="18" cy="42" r="3"/><circle cx="42" cy="42" r="3"/></svg></span>Community Access</div>

  <div class="contact contact-phone"><svg viewBox="0 0 24 24" fill="var(--teal)"><path d="M6 2 L10 6 L8 9 C9 12 12 15 15 16 L18 14 L22 18 L19 22 C10 21 3 14 2 5 Z"/></svg>+61 0400 123 456</div>
  <div class="contact contact-email"><svg viewBox="0 0 24 24" fill="var(--teal)"><rect x="2" y="5" width="20" height="14"/><path d="M2 5 L12 13 L22 5" stroke="var(--ink)" stroke-width="2" fill="none"/></svg>hello@clearviewcare.com.au</div>

  <div class="socials" aria-label="KTAP registration and social links">
    <span class="social-badge social-badge--round"></span>
    <span class="social-badge" style="background:#1877f2"></span>
    <span class="social-badge" style="background:var(--pink)"></span>
    <span class="social-badge" style="background:#0a66c2"></span>
  </div>
  <div class="web"><svg viewBox="0 0 24 24" fill="none" stroke="var(--purple)" stroke-width="2"><circle cx="12" cy="12" r="10"/><path d="M2 12 H22 M12 2 C7 8 7 16 12 22 C17 16 17 8 12 2"/></svg>www.clearviewcare.com.au</div>
</main>
</body>
</html>
```